Dovecote Realty

Business cards for 4 people

They need to say for all
87 Tarrow Quay, Boston MA 02114

Each person will have their own personal information
We would like gold embossing for the name of the company
Marla is the blonde sitting in the chair smiling her information should be on the back of the card with her name and information
Should say for slogan classic pattern, elevated experience
grace@dovecoteprops.com
(413) 555-0182

Odette is the brunette with wavy hair in the tan suit odette@dovecoteprops.com
(617) 555-0137

faith@dovecoteprops.com
(413) 555-0164
standing next to the chair

hope@dovecoteprops.com
(413) 555-0199
close up headshot

```html
<!DOCTYPE html>
<html lang="en">
<head>
<meta charset="utf-8">
<title>Dovecote Realty – Business Cards</title>
<link href="https://fonts.googleapis.com/css2?family=Open+Sans:wght@400;600;700&display=swap" rel="stylesheet">
<style>
  :root {
    --stage: #222222;
    --card-dark: #1c1c1f;
    --gold: #e9b96a;
    --gold-deep: #c8923a;
    --gold-band: #b98d4f;
    --ink-light: #ffffff;
    --photo-light: #fbf8ef;
    --photo-hair: #7a5535;
  }
  * { box-sizing: border-box; margin: 0; padding: 0; }
  html, body { width: 1200px; height: 780px; overflow: hidden; }
  body {
    background: var(--stage);
    font-family: "Open Sans", Arial, sans-serif;
    position: relative;
  }
  .card {
    position: absolute;
    top: 236px;
    width: 530px;
    height: 303px;
    border-radius: 3px;
    overflow: hidden;
  }
  .card--front { left: 52px; background: var(--card-dark); }
  .card--back { left: 618px; background: var(--gold); }

  .brand {
    position: absolute;
    display: flex;
    align-items: center;
    gap: 8px;
    font-weight: 600;
    letter-spacing: 0.06em;
    text-transform: uppercase;
    white-space: nowrap;
  }
  .brand__dot {
    border-radius: 50%;
    border: 2px solid currentColor;
  }
  .card--front .brand {
    top: 26px; left: 150px;
    color: var(--gold);
    font-size: 15px;
  }
  .card--front .brand__dot { width: 40px; height: 40px; }
  .card--back .brand {
    top: 50%; left: 50%;
    transform: translate(-50%, -50%);
    color: var(--gold-deep);
    font-size: 30px;
    gap: 16px;
  }
  .card--back .brand__dot { width: 92px; height: 92px; border-width: 3px; }

  .name-band {
    position: absolute;
    top: 82px; left: 0;
    width: 330px; height: 64px;
    padding: 8px 0 0 60px;
    background: linear-gradient(90deg, var(--gold-band) 0%, rgba(185,141,79,0.55) 55%, rgba(28,28,31,0) 100%);
  }
  .name-band__name {
    color: var(--ink-light);
    font-weight: 700;
    font-size: 26px;
    line-height: 1.1;
    white-space: nowrap;
  }
  .name-band__title {
    color: var(--ink-light);
    font-size: 10.5px;
    margin-top: 3px;
    white-space: nowrap;
  }

  .contact {
    position: absolute;
    top: 158px; left: 32px;
    color: var(--gold);
    font-size: 12.5px;
    line-height: 1.5;
    list-style: none;
  }
  .contact__address { padding-left: 28px; margin-bottom: 2px; }
  .contact__item { display: flex; align-items: center; gap: 10px; }
  .contact__icon { width: 14px; height: 14px; fill: none; stroke: var(--gold); stroke-width: 1.6; }

  .portrait {
    position: absolute;
    top: 104px; right: 40px;
    width: 180px; height: 180px;
    border-radius: 50%;
    border: 4px solid var(--gold);
    background: linear-gradient(180deg, var(--photo-light) 0%, var(--photo-light) 25%, var(--photo-hair) 60%, #9a7656 100%);
  }
</style>
</head>
<body>

<section class="card card--front" aria-label="Business card front">
  <div class="brand"><span>Dovecote Realty</span><span class="brand__dot"></span></div>

  <div class="name-band">
    <p class="name-band__name">Odette Marchand</p>
    <p class="name-band__title">Real Estate Advisor and Sales Manager</p>
  </div>

  <ul class="contact">
    <li class="contact__address">87 Tarrow Quay,<br>Boston MA 02114</li>
    <li class="contact__item">
      <svg class="contact__icon" viewBox="0 0 16 16"><path d="M4 1.5l2.5 3-1.5 1.8c.8 1.8 2.2 3.2 4 4l1.8-1.5 3 2.5-1.3 2.2C7.5 13.5 2.5 8.5 2 3z"/></svg>
      <span>(617) 555-0137</span>
    </li>
    <li class="contact__item">
      <svg class="contact__icon" viewBox="0 0 16 16"><circle cx="8" cy="8" r="6.5"/><path d="M1.5 8h13M8 1.5c-3 3.5-3 9.5 0 13M8 1.5c3 3.5 3 9.5 0 13"/></svg>
      <span>www.dovecoteprops.com</span>
    </li>
    <li class="contact__item">
      <svg class="contact__icon" viewBox="0 0 16 16"><rect x="1.5" y="3.5" width="13" height="9"/><path d="M1.5 3.5L8 9l6.5-5.5"/></svg>
      <span>odette@dovecoteprops.com</span>
    </li>
  </ul>

  <div class="portrait" role="img" aria-label="Portrait photo of Odette, brunette with wavy hair in a tan suit"></div>
</section>

<section class="card card--back" aria-label="Business card back">
  <div class="brand"><span>Dovecote Realty</span><span class="brand__dot"></span></div>
</section>

</body>
</html>
```